Business Card Design

Hi I need a business card designed, we already have the business name logo artwork and would like some concept ideas for the Bus Card layout.
On the back of the card i want to include the products and services that we offer.
We are a Plastics Sheeting manufacture based in Perth Australia.

                                       

We need a BC design for a company called Tarvo Plastics based in Perth Australia.

We supply from DIY to Trade & Industrial  Engineering Markets.

We specialise in:

·         Cut to size panels  (all shapes and sizes)

·         Plastics fabrication & Welding

·         Custom Designs

·         Plastic Repairs

·         PVC Pipe Slotting & PVC Pipe Threading

·         Supplier of all types of engineering plastics and profiles.

Including:           Acrylic / Clarvene

                               Polycarbonate / Dorvil

                               Prismatic Light Diffuser

                               Vantrib

                               HDPE / UHMWPE

                               PVC / PVC Foam

                               Nylon

                               HIPS

```html
<!DOCTYPE html>
<html lang="en">
<head>
<meta charset="utf-8">
<title>Tarvo Plastics – Business Card</title>
<link href="https://fonts.googleapis.com/css2?family=Open+Sans:wght@400;600;700;800&display=swap" rel="stylesheet">
<style>
  :root {
    --navy: #1d2b6e;
    --blue: #2d83c5;
    --orange: #f0891c;
    --grey: #555a60;
    --rule: #c9ccd2;
    --paper: #ffffff;
    --backdrop: #e9e7e3;
  }
  * { box-sizing: border-box; margin: 0; padding: 0; }
  html, body { width: 1200px; height: 720px; overflow: hidden; }
  body {
    background: var(--backdrop);
    font-family: "Open Sans", Arial, sans-serif;
    position: relative;
  }
  .card {
    position: absolute;
    top: 205px;
    width: 540px;
    height: 310px;
    background: var(--paper);
    box-shadow: 0 6px 18px rgba(0,0,0,.18);
    overflow: hidden;
  }
  .card--front { left: 40px; }
  .card--back { left: 620px; }

  /* Front */
  .brand {
    position: absolute; top: 34px; left: 0; right: 0;
    display: flex; justify-content: center; align-items: center; gap: 12px;
  }
  .brand__mark { width: 24px; height: 24px; background: var(--orange); }
  .brand__name {
    font-size: 44px; font-weight: 800; color: var(--navy); letter-spacing: -0.5px;
  }
  .band {
    position: absolute; top: 118px; left: 0; right: 0; height: 30px;
    background: var(--blue);
    border-top: 3px solid var(--navy);
    color: #fff; font-size: 12.5px; font-weight: 600;
    display: flex; align-items: center; justify-content: flex-end; padding-right: 20px;
  }
  .band--foot { top: auto; bottom: 22px; height: 10px; border-top: none; border-bottom: 2px solid var(--navy); }
  .contact-area {
    position: absolute; top: 156px; left: 0; right: 0; height: 124px;
    display: flex;
  }
  .person {
    width: 262px; text-align: right; padding-right: 16px;
    border-right: 1px solid var(--rule);
  }
  .person__name { font-size: 17px; font-weight: 700; color: var(--navy); line-height: 1.2; }
  .person__title { font-size: 13px; color: var(--orange); line-height: 1.3; margin-bottom: 4px; }
  .person__address { font-size: 12.5px; color: var(--grey); line-height: 1.4; font-style: normal; }
  .details { list-style: none; padding: 2px 0 0 14px; }
  .details li {
    display: flex; align-items: center; gap: 8px;
    font-size: 13px; color: var(--grey); line-height: 1; height: 25px;
  }
  .details svg { width: 13px; height: 13px; flex: none; }

  /* Back */
  .offer {
    position: absolute; inset: 0; padding: 26px 24px 0;
    text-align: center; color: var(--navy);
  }
  .offer__intro { font-size: 13.5px; font-weight: 700; line-height: 1.3; }
  .offer__heading { font-size: 18px; font-weight: 700; margin: 10px 0 4px; }
  .offer__list { list-style: none; font-size: 12.5px; color: var(--grey); line-height: 1.55; }
  .offer__list li { display: inline; margin: 0 5px; }
  .offer__list li::before {
    content: ""; display: inline-block; width: 6px; height: 6px; border-radius: 50%;
    background: var(--blue); margin-right: 5px; vertical-align: middle;
  }
  .offer__row { display: block; }
</style>
</head>
<body>

<section class="card card--front" aria-label="Business card front">
  <div class="brand">
    <span class="brand__mark"></span>
    <span class="brand__name">Tarvo Plastics</span>
  </div>

  <div class="band">Tarvo Holdings Pty Ltd T/A Tarvo Plastics ABN: TBA</div>

  <div class="contact-area">
    <div class="person">
      <p class="person__name">Your Name</p>
      <p class="person__title">Title</p>
      <address class="person__address">
        Unit 4/18 Kestrel Circuit<br>
        Bayswater WA 6053<br>
        PO Box 2240<br>
        Bayswater DC WA 6933
      </address>
    </div>
    <ul class="details">
      <li>
        <svg viewBox="0 0 16 16" aria-hidden="true"><circle cx="8" cy="8" r="7" fill="none" stroke="var(--orange)" stroke-width="1.6"/><path d="M5.5 4.5l1.6 1.6-.9 1.1a6 6 0 0 0 2.6 2.6l1.1-.9 1.6 1.6-1 1.2c-2.6-.4-5.3-3.1-5.7-5.7z" fill="var(--orange)"/></svg>
        08 9400 1120
      </li>
      <li>
        <svg viewBox="0 0 16 16" aria-hidden="true"><rect x="4" y="1" width="8" height="14" rx="1.5" fill="var(--orange)"/><rect x="5.5" y="3" width="5" height="7" fill="#fff"/></svg>
        0400 555 018
      </li>
      <li>
        <svg viewBox="0 0 16 16" aria-hidden="true"><rect x="1" y="6" width="14" height="7" rx="1.5" fill="var(--orange)"/><rect x="4" y="2" width="8" height="5" fill="var(--orange)"/><rect x="5" y="3" width="6" height="3" fill="#fff"/></svg>
        08 9400 1122
      </li>
      <li>
        <svg viewBox="0 0 16 16" aria-hidden="true"><rect x="1" y="3" width="14" height="10" rx="1.5" fill="var(--orange)"/><path d="M2 4.5l6 4.5 6-4.5" fill="none" stroke="#fff" stroke-width="1.4"/></svg>
        sales@tarvoplastics.com.au
      </li>
    </ul>
  </div>

  <div class="band band--foot"></div>
</section>

<section class="card card--back" aria-label="Business card back">
  <div class="offer">
    <p class="offer__intro">The Products And Services That We Offer<br>Are Supplied From Diy To Trade &amp; Industrial Engineering Markets</p>

    <h2 class="offer__heading">We specialise in:</h2>
    <ul class="offer__list">
      <span class="offer__row"><li>Cut to size panels (all shapes and sizes)</li></span>
      <span class="offer__row"><li>Plastics fabrication &amp; Welding</li><li>Custom Designs</li></span>
      <span class="offer__row"><li>Plastic Repairs</li><li>PVC Pipe Slotting &amp; PVC Pipe Threading</li></span>
      <span class="offer__row"><li>Supplier of all types of engineering plastics and profiles</li></span>
    </ul>

    <h2 class="offer__heading">Including:</h2>
    <ul class="offer__list">
      <span class="offer__row"><li>Acrylic / Clarvene</li><li>Polycarbonate / Dorvil</li></span>
      <span class="offer__row"><li>Prismatic Light Diffuser</li><li>Vantrib</li><li>HDPE / UHMWPE</li></span>
      <span class="offer__row"><li>PVC / PVC Foam</li><li>Nylon</li><li>HIPS</li></span>
    </ul>
  </div>
</section>

</body>
</html>
```